1 Page for Computer Repair Website

Looking for a 1 page website with a design that compliments the business card and pamphlet that have already been made (attached files). It should look business professional and easy to read. Email and phone number should be somewhere near the top of the website, visible when the page loads. I don't want any forms for people to mess with. No "Contact Us" form or entering in email for newsletter. Customers will just be looking at this site to confirm we are professionals and have our business in order.

Target Market(s)

Home and small business

Industry/Entity Type

Computer Repair

Coding

Coded - Design and coding required

Number of Pages Required

1 page

Font styles to use
Other font styles liked:
• Helvetica variations used in pamphlet and card

Colors
0455a3
cfdeed
85abd2
3276b5
85cae6
ffffff

Requirements
Must have
• Compliment the pamphlet and business card in color choices and font use. Pleasing to the eye and easy to read through categories and text.
Should not have
• Forms. No "enter name and email here" or anything of the sort.

```html
<!DOCTYPE html>
<html lang="en">
<head>
<meta charset="utf-8">
<title>Pulsetech Computer Services</title>
<link href="https://fonts.googleapis.com/css2?family=Roboto:wght@300;400;500;700;900&display=swap" rel="stylesheet">
<style>
:root{
  --brand:#0455a3;
  --brand-mid:#3276b5;
  --brand-soft:#85abd2;
  --sky:#85cae6;
  --mist:#cfdeed;
  --hero:#1aa0da;
  --ink:#222a33;
  --muted:#5d6670;
  --dark:#1f1c19;
  --white:#ffffff;
  --footer-deep:#033f7a;
  --star:#e0a323;
}
*{margin:0;padding:0;box-sizing:border-box}
html,body{width:1200px;height:2668px;overflow:hidden}
body{font-family:"Roboto",Arial,sans-serif;color:var(--ink);background:var(--white)}
.site-header{height:100px;display:flex;align-items:center;justify-content:space-between;padding:0 60px}
.brand{display:flex;flex-direction:column}
.brand-name{font-size:34px;font-weight:700;color:var(--brand);letter-spacing:1px;line-height:1}
.brand-tag{font-size:13px;color:var(--muted);margin-top:4px;letter-spacing:1px}
.contact-top{display:flex;align-items:center;gap:14px}
.contact-top .icon{width:44px;height:44px;border-radius:50%;background:var(--brand);display:flex;align-items:center;justify-content:center}
.contact-lines{display:flex;flex-direction:column;line-height:1.1}
.contact-lines .mail{font-size:15px;color:var(--muted)}
.contact-lines .phone{font-size:28px;font-weight:700;color:var(--brand)}
.main-nav{height:44px;background:var(--brand-mid);display:flex;justify-content:center}
.main-nav a{display:block;width:128px;line-height:44px;text-align:center;color:var(--white);font-size:14px;text-decoration:none}
.main-nav a.active{background:var(--brand)}
.hero{position:relative;height:400px;background:linear-gradient(180deg,#27addf 0%,var(--hero) 100%);color:var(--white);padding:70px 80px 0}
.hero-kicker{font-size:30px;font-weight:500;letter-spacing:1px}
.hero-title{font-size:50px;font-weight:700;line-height:1.05;letter-spacing:.5px}
.hero-sub{font-size:36px;font-weight:400;margin-top:4px;letter-spacing:1px}
.hero-text{font-size:15px;margin-top:20px;max-width:640px;opacity:.95}
.btn-solid{display:inline-block;margin-top:30px;background:var(--brand);color:var(--white);font-size:16px;font-weight:500;padding:14px 34px;text-decoration:none}
.hero-visual{position:absolute;left:760px;top:44px;width:380px;height:290px;border-radius:6px;background:linear-gradient(160deg,#e8eef3 0%,#9fb3c4 55%,#3d4a57 100%)}
.hero-dots{position:absolute;left:0;right:0;bottom:24px;display:flex;justify-content:center;gap:10px}
.hero-dots span{width:10px;height:10px;border-radius:50%;background:rgba(255,255,255,.5)}
.hero-dots span.on{background:var(--white)}
.services{height:966px;padding-top:56px}
.section-title{text-align:center;font-size:42px;font-weight:500;color:var(--ink)}
.title-rule{width:60px;height:3px;background:var(--brand);margin:16px auto 0}
.service-grid{display:grid;grid-template-columns:repeat(4,240px);column-gap:40px;row-gap:90px;padding:90px 80px 0}
.service-head{display:flex;align-items:center;gap:12px}
.service-icon{width:54px;height:54px;border-radius:50%;background:var(--brand);display:flex;align-items:center;justify-content:center;flex:none}
.service-num{font-size:56px;font-weight:500;color:var(--ink);line-height:1}
.service-name{font-size:17px;font-weight:700;margin-top:16px;line-height:1.25;color:var(--ink)}
.service-text{font-size:14px;line-height:1.55;color:var(--muted);margin-top:10px}
.about{position:relative;height:430px;color:var(--white);text-align:center;padding-top:60px}
.about-bg{position:absolute;inset:0;background:linear-gradient(180deg,#2b2723 0%,var(--dark) 60%,#14120f 100%)}
.about-inner{position:relative;padding:0 80px}
.about h2{font-size:38px;font-weight:500;letter-spacing:1px}
.about .title-rule{background:var(--white)}
.about p{font-size:15px;line-height:1.7;margin:36px auto 0;max-width:1040px;text-align:left;opacity:.9}
.btn-outline{display:inline-block;margin-top:44px;border:2px solid var(--white);color:var(--white);font-size:15px;padding:14px 40px;text-decoration:none;letter-spacing:1px}
.testimonials{height:404px;padding-top:50px}
.stars{display:flex;justify-content:center;gap:6px;margin-top:18px}
.quotes{display:grid;grid-template-columns:repeat(2,1fr);column-gap:80px;padding:34px 100px 0}
.quote{display:flex;gap:24px;align-items:flex-start}
.avatar{width:130px;height:130px;border-radius:50%;flex:none;background:linear-gradient(160deg,#d9c5b4,#8a7462)}
.quote-stars{display:flex;gap:4px}
.quote p{font-size:14px;line-height:1.55;color:var(--muted);margin-top:8px}
.quote cite{display:block;font-style:normal;font-size:16px;margin-top:10px;color:var(--ink)}
.site-footer{height:276px;background:var(--brand);display:grid;grid-template-columns:1.3fr 1fr 1fr;align-content:center;padding:0 80px;row-gap:56px;color:var(--white)}
.foot-item{display:flex;align-items:center;gap:20px;font-size:17px;line-height:1.4}
.foot-icon{width:60px;height:60px;background:var(--footer-deep);display:flex;align-items:center;justify-content:center;flex:none}
.legal{height:48px;background:var(--footer-deep);color:var(--mist);font-size:13px;text-align:center;line-height:48px}
</style>
</head>
<body>
<header class="site-header">
  <div class="brand">
    <span class="brand-name">PULSETECH</span>
    <span class="brand-tag">Computer Services</span>
  </div>
  <div class="contact-top">
    <div class="icon"><svg width="22" height="22" viewBox="0 0 24 24" fill="#fff"><path d="M6.6 10.8a15.1 15.1 0 006.6 6.6l2.2-2.2a1 1 0 011-.25 11.4 11.4 0 003.6.57 1 1 0 011 1V20a1 1 0 01-1 1A17 17 0 013 4a1 1 0 011-1h3.5a1 1 0 011 1c0 1.25.2 2.450.57 3.57a1 1 0 01-.25 1z"/></svg></div>
    <div class="contact-lines">
      <span class="mail">info@pulsetech.example</span>
      <span class="phone">888-555-0147</span>
    </div>
  </div>
</header>

<nav class="main-nav">
  <a class="active" href="#">Home</a><a href="#">About</a><a href="#">Services</a><a href="#">Approach</a><a href="#">Support</a><a href="#">Reviews</a><a href="#">Contact</a>
</nav>

<section class="hero">
  <div class="hero-kicker">COMPUTER</div>
  <div class="hero-title">REPAIR AND SUPPORT</div>
  <div class="hero-sub">ANYTIME, ANYWHERE</div>
  <p class="hero-text">Fast, friendly and honest computer care for homes and small businesses across the area.</p>
  <a class="btn-solid" href="#">Know More</a>
  <div class="hero-visual" role="img" aria-label="Desktop computer monitor with keyboard and mouse"></div>
  <div class="hero-dots"><span></span><span></span><span class="on"></span><span></span><span></span></div>
</section>

<section class="services">
  <h2 class="section-title">Our Services</h2>
  <div class="title-rule"></div>
  <div class="service-grid">
    <article>
      <div class="service-head"><div class="service-icon"><svg width="26" height="26" viewBox="0 0 24 24" fill="#fff"><path d="M12 2l8 3v6c0 5-3.4 9.4-8 11-4.6-1.6-8-6-8-11V5z"/></svg></div><span class="service-num">01</span></div>
      <h3 class="service-name">Malware/<br>Virus Removal</h3>
      <p class="service-text">Infections can slow your machine, steal your files and flood the screen with pop-ups. We remove malware, clean up the damage and set up protection so it stays gone for good.</p>
    </article>
    <article>
      <div class="service-head"><div class="service-icon"><svg width="26" height="26" viewBox="0 0 24 24" fill="#fff"><path d="M3 4h18v12H3zM9 18h6v2H9z"/></svg></div><span class="service-num">02</span></div>
      <h3 class="service-name">PC/Desktop/<br>Laptop Hardware Repair</h3>
      <p class="service-text">Find out exactly which part of your computer is failing and why. Our technicians replace screens, keyboards, drives and batteries with quality parts and test every repair before it goes home.</p>
    </article>
    <article>
      <div class="service-head"><div class="service-icon"><svg width="26" height="26" viewBox="0 0 24 24" fill="#fff"><path d="M12 3l7 8h-4v9H9v-9H5z"/></svg></div><span class="service-num">03</span></div>
      <h3 class="service-name">Upgrades<br>Hassle Free</h3>
      <p class="service-text">A new video card, more memory or a faster drive can give an older machine a second life. We help you choose the right parts and install them the same day.</p>
    </article>
    <article>
      <div class="service-head"><div class="service-icon"><svg width="26" height="26" viewBox="0 0 24 24" fill="#fff"><ellipse cx="12" cy="5" rx="8" ry="3"/><path d="M4 7v5c0 1.7 3.6 3 8 3s8-1.3 8-3V7c0 1.7-3.6 3-8 3S4 8.7 4 7zM4 14v5c0 1.7 3.6 3 8 3s8-1.3 8-3v-5c0 1.7-3.6 3-8 3s-8-1.3-8-3z"/></svg></div><span class="service-num">04</span></div>
      <h3 class="service-name">Data<br>Migration</h3>
      <p class="service-text">Moving to a new computer? We carry over your files, photos, bookmarks, email accounts and settings so your new machine feels familiar from the very first time you switch it on.</p>
    </article>
    <article>
      <div class="service-head"><div class="service-icon"><svg width="26" height="26" viewBox="0 0 24 24" fill="none" stroke="#fff" stroke-width="2.4"><path d="M20 12a8 8 0 11-2.3-5.7M20 4v5h-5"/></svg></div><span class="service-num">05</span></div>
      <h3 class="service-name">Data Rescue</h3>
      <p class="service-text">Deleted a folder by mistake or heard a drive start clicking? Stop using it and call us. We recover documents, photos and records from damaged disks, cards and flash drives.</p>
    </article>
    <article>
      <div class="service-head"><div class="service-icon"><svg width="26" height="26" viewBox="0 0 24 24" fill="none" stroke="#fff" stroke-width="2.4"><circle cx="12" cy="12" r="7"/><path d="M12 12l4-3"/></svg></div><span class="service-num">06</span></div>
      <h3 class="service-name">Tune Ups</h3>
      <p class="service-text">Slow start-ups and random freezes wear down your day. We clear out clutter, update drivers, check hard drive health and tidy startup programs so your computer runs at peak speed again.</p>
    </article>
    <article>
      <div class="service-head"><div class="service-icon"><svg width="26" height="26" viewBox="0 0 24 24" fill="#fff"><path d="M12 3l9 8h-3v9h-5v-6h-2v6H6v-9H3z"/></svg></div><span class="service-num">07</span></div>
      <h3 class="service-name">In-Home Installation</h3>
      <p class="service-text">Our technicians come to you to set up new computers, printers, routers and home networks. Everything is connected, tested and explained before we leave, so nothing is left to guesswork.</p>
    </article>
    <article>
      <div class="service-head"><div class="service-icon"><svg width="26" height="26" viewBox="0 0 24 24" fill="#fff"><path d="M2 5h14v10H2zM6 17h6v2H6zM18 8h4v11h-4z"/></svg></div><span class="service-num">08</span></div>
      <h3 class="service-name">Remote Support</h3>
      <p class="service-text">Small problems rarely need a visit. With your permission we connect to your computer securely over the internet, fix the issue while you watch and you carry on with your day.</p>
    </article>
  </div>
</section>

<section class="about">
  <div class="about-bg" role="img" aria-label="Dark workshop desk with computer parts and tools"></div>
  <div class="about-inner">
    <h2>LITTLE ABOUT US</h2>
    <div class="title-rule"></div>
    <p>We are a local team of certified technicians with more than fifteen years of experience keeping home and office computers running. From a single laptop to a small business network, we diagnose problems quickly, explain every option in plain language and quote a fair price before any work begins. Our clients trust us because we show up on time, protect their data and stand behind every repair we make.</p>
    <a class="btn-outline" href="#">KNOW MORE</a>
  </div>
</section>

<section class="testimonials">
  <h2 class="section-title">Testimonials</h2>
  <div class="stars">
    <svg width="16" height="16" viewBox="0 0 24 24" fill="#e0a323"><path d="M12 2l3 7h7l-5.5 4.5 2 7.5L12 16.8 5.5 21l2-7.5L2 9h7z"/></svg>
    <svg width="16" height="16" viewBox="0 0 24 24" fill="#e0a323"><path d="M12 2l3 7h7l-5.5 4.5 2 7.5L12 16.8 5.5 21l2-7.5L2 9h7z"/></svg>
    <svg width="16" height="16" viewBox="0 0 24 24" fill="#e0a323"><path d="M12 2l3 7h7l-5.5 4.5 2 7.5L12 16.8 5.5 21l2-7.5L2 9h7z"/></svg>
  </div>
  <div class="quotes">
    <div class="quote">
      <div class="avatar" role="img" aria-label="Portrait of a smiling customer"></div>
      <div>
        <div class="quote-stars">
          <svg width="14" height="14" viewBox="0 0 24 24" fill="#e0a323"><path d="M12 2l3 7h7l-5.5 4.5 2 7.5L12 16.8 5.5 21l2-7.5L2 9h7z"/></svg><svg width="14" height="14" viewBox="0 0 24 24" fill="#e0a323"><path d="M12 2l3 7h7l-5.5 4.5 2 7.5L12 16.8 5.5 21l2-7.5L2 9h7z"/></svg><svg width="14" height="14" viewBox="0 0 24 24" fill="#e0a323"><path d="M12 2l3 7h7l-5.5 4.5 2 7.5L12 16.8 5.5 21l2-7.5L2 9h7z"/></svg><svg width="14" height="14" viewBox="0 0 24 24" fill="#e0a323"><path d="M12 2l3 7h7l-5.5 4.5 2 7.5L12 16.8 5.5 21l2-7.5L2 9h7z"/></svg><svg width="14" height="14" viewBox="0 0 24 24" fill="#e0a323"><path d="M12 2l3 7h7l-5.5 4.5 2 7.5L12 16.8 5.5 21l2-7.5L2 9h7z"/></svg>
        </div>
        <p>My laptop died the night before a big deadline. They had it running again by morning and saved every file. Friendly, fast and fairly priced. I would not go anywhere else.</p>
        <cite>- Mira</cite>
      </div>
    </div>
    <div class="quote">
      <div class="avatar" role="img" aria-label="Portrait of a satisfied business client"></div>
      <div>
        <div class="quote-stars">
          <svg width="14" height="14" viewBox="0 0 24 24" fill="#e0a323"><path d="M12 2l3 7h7l-5.5 4.5 2 7.5L12 16.8 5.5 21l2-7.5L2 9h7z"/></svg><svg width="14" height="14" viewBox="0 0 24 24" fill="#e0a323"><path d="M12 2l3 7h7l-5.5 4.5 2 7.5L12 16.8 5.5 21l2-7.5L2 9h7z"/></svg><svg width="14" height="14" viewBox="0 0 24 24" fill="#e0a323"><path d="M12 2l3 7h7l-5.5 4.5 2 7.5L12 16.8 5.5 21l2-7.5L2 9h7z"/></svg><svg width="14" height="14" viewBox="0 0 24 24" fill="#e0a323"><path d="M12 2l3 7h7l-5.5 4.5 2 7.5L12 16.8 5.5 21l2-7.5L2 9h7z"/></svg><svg width="14" height="14" viewBox="0 0 24 24" fill="#e0a323"><path d="M12 2l3 7h7l-5.5 4.5 2 7.5L12 16.8 5.5 21l2-7.5L2 9h7z"/></svg>
        </div>
        <p>They set up the whole network for our office and still answer the phone whenever we need help. Clear advice, no jargon and no surprise bills. Highly recommended to any small business.</p>
        <cite>- Daniel Hart</cite>
      </div>
    </div>
  </div>
</section>

<footer class="site-footer">
  <div class="foot-item"><div class="foot-icon"><svg width="28" height="28" viewBox="0 0 24 24" fill="#fff"><path d="M12 3l9 8h-3v9h-5v-6h-2v6H6v-9H3z"/></svg></div><span>418 Harbor Lane, Suite #210<br>Lakeview FL 33400 USA</span></div>
  <div class="foot-item"><div class="foot-icon"><svg width="26" height="26" viewBox="0 0 24 24" fill="#fff"><path d="M6.6 10.8a15.1 15.1 0 006.6 6.6l2.2-2.2a1 1 0 011-.25 11.4 11.4 0 003.6.57 1 1 0 011 1V20a1 1 0 01-1 1A17 17 0 013 4a1 1 0 011-1h3.5a1 1 0 011 1c0 1.25.2 2.45.57 3.57a1 1 0 01-.25 1z"/></svg></div><span>+1 (555) 014 2268</span></div>
  <div class="foot-item"><div class="foot-icon"><svg width="22" height="22" viewBox="0 0 24 24"><circle cx="12" cy="12" r="9" fill="#fff"/></svg></div><span>Community</span></div>
  <div class="foot-item"><div class="foot-icon"><svg width="28" height="28" viewBox="0 0 24 24" fill="#fff"><path d="M2 5h20v14H2zm2 2v.5l8 5 8-5V7l-8 5z" fill-rule="evenodd"/></svg></div><span>info@pulsetech.example</span></div>
  <div class="foot-item"><div class="foot-icon"><svg width="26" height="26" viewBox="0 0 24 24" fill="#fff"><path d="M6.6 10.8a15.1 15.1 0 006.6 6.6l2.2-2.2a1 1 0 011-.25 11.4 11.4 0 003.6.57 1 1 0 011 1V20a1 1 0 01-1 1A17 17 0 013 4a1 1 0 011-1h3.5a1 1 0 011 1c0 1.25.2 2.45.57 3.57a1 1 0 01-.25 1z"/></svg></div><span>+1 (555) 019 3371</span></div>
  <div class="foot-item"><div class="foot-icon"><svg width="22" height="22" viewBox="0 0 24 24"><rect x="3" y="3" width="18" height="18" fill="#fff"/></svg></div><span>Updates</span></div>
</footer>
<div class="legal">2015 Copyright. All rights reserved by pulsetech.example</div>
</body>
</html>
```